Whitcombe Business Card Design

The name of the business is Dario Whitcombe, CPA LLC
The service that we offer is Accounting, Tax & Consulting Services. I need it to have the following items:
Dario Whitcombe, Principal
Phone Number
Email Address
Physical Address

I have attached the company logo, one in black and one in white. Please provide a design in black background and the other in white background. Please include "Accounting, Tax & Consulting Services". I want the business card to be clean and very professional.

```html
<!DOCTYPE html>
<html lang="en">
<head>
<meta charset="utf-8">
<title>Dario Whitcombe, CPA LLC — Business Card</title>
<link href="https://fonts.googleapis.com/css2?family=Montserrat:wght@400;500;600&display=swap" rel="stylesheet">
<style>
  :root {
    --backdrop: #d3d3d3;
    --card: #ffffff;
    --card-dark: #1c1c1c;
    --ink-dark: #363636;
    --ink-light: #ffffff;
    --ink-grey: #8a8a8a;
    --ink-grey-light: #b4b4b4;
    --ink-body: #767676;
    --brand-red: #9b1b1e;
    --rule: #9c9c9c;
  }
  * { margin: 0; padding: 0; box-sizing: border-box; }
  html, body {
    width: 1000px; height: 1200px; overflow: hidden;
    background: var(--backdrop);
    font-family: "Montserrat", Arial, sans-serif;
  }
  .canvas { position: relative; width: 1000px; height: 1200px; }
  .card {
    position: absolute; left: 134px; width: 732px; height: 418px;
    background: var(--card);
    box-shadow: 2px 4px 6px rgba(0,0,0,0.35);
    overflow: hidden;
  }
  .card--front { top: 160px; }
  .card--back { top: 622px; background: var(--card-dark); }

  .brand-square { position: absolute; background: var(--brand-red); }
  .brand-name {
    position: absolute; white-space: nowrap;
    color: var(--ink-dark); font-weight: 600; text-transform: uppercase;
    letter-spacing: 0.3px; line-height: 1.2;
  }
  .brand-tagline {
    position: absolute; white-space: nowrap;
    color: var(--ink-grey); font-weight: 600; text-transform: uppercase;
    letter-spacing: 3.4px; line-height: 1.2;
  }
  .brand-services {
    position: absolute; white-space: nowrap;
    color: var(--ink-grey); font-weight: 500;
    letter-spacing: 1px; line-height: 1.2;
  }

  /* front */
  .card--front .brand-square { left: 65px; top: 49px; width: 75px; height: 75px; }
  .card--front .brand-name { left: 167px; top: 50px; font-size: 30px; }
  .card--front .brand-tagline { left: 167px; top: 92px; font-size: 21px; }
  .card--front .brand-services { left: 167px; top: 130px; font-size: 14px; }

  .person { position: absolute; left: 0; right: 0; top: 202px; text-align: center; }
  .person__name { color: var(--brand-red); font-size: 25px; font-weight: 600; line-height: 1.2; }
  .person__role { color: var(--ink-grey); font-size: 17px; margin-top: 4px; }

  .divider { position: absolute; left: 64px; right: 65px; top: 279px; height: 1px; background: var(--rule); }

  .contact-list, .address {
    position: absolute; top: 300px; list-style: none;
    color: var(--ink-body); font-size: 18px; line-height: 25px;
  }
  .contact-list { left: 65px; }
  .contact-list li { display: flex; align-items: center; gap: 12px; }
  .contact-list svg { width: 15px; height: 15px; fill: var(--brand-red); flex: none; }
  .address { right: 65px; text-align: right; font-style: normal; }

  /* back (dark) */
  .card--back .brand-square { left: 312px; top: 100px; width: 107px; height: 107px; }
  .card--back .brand-name { left: 0; right: 0; top: 224px; text-align: center; font-size: 28px; color: var(--ink-light); }
  .card--back .brand-tagline { left: 0; right: 0; top: 262px; text-align: center; font-size: 20px; color: var(--ink-grey-light); }
  .card--back .brand-services { left: 0; right: 0; top: 300px; text-align: center; font-size: 15px; color: var(--ink-grey-light); }
</style>
</head>
<body>
<main class="canvas">
  <section class="card card--front" aria-label="Card front, white background">
    <div class="brand-square" aria-hidden="true"></div>
    <div class="brand-name">Dario Whitcombe, CPA, LLC</div>
    <div class="brand-tagline">Certified Public Accountant</div>
    <div class="brand-services">Accounting, Tax &amp; Consulting Services</div>

    <div class="person">
      <div class="person__name">Dario Whitcombe</div>
      <div class="person__role">Principal</div>
    </div>

    <div class="divider"></div>

    <ul class="contact-list">
      <li>
        <svg viewBox="0 0 16 16" aria-hidden="true"><path d="M3.5 1.2l2.4 2.6-1.4 1.8c.9 2 2.7 3.9 4.7 4.9l1.8-1.4 2.6 2.4-1.6 2.3C7.2 13.6 2.4 8.8 1.3 3.1z"/></svg>
        <span>1-800-555-0147</span>
      </li>
      <li>
        <svg viewBox="0 0 16 16" aria-hidden="true"><path d="M1 3.5h14v1.2L8 9 1 4.7z M1 6.2l7 4.3 7-4.3V12.5H1z"/></svg>
        <span>info@website.com</span>
      </li>
      <li>
        <svg viewBox="0 0 16 16" aria-hidden="true"><path d="M8 1a7 7 0 1 0 0 14A7 7 0 0 0 8 1zm0 1.4c.8.8 1.4 2.2 1.6 3.8H6.4C6.6 4.6 7.2 3.2 8 2.4zM2.5 7.3h2.8c0 .5 0 1 .1 1.4H2.5a5.6 5.6 0 0 1 0-1.4zm3.9 0h3.2a9 9 0 0 1 0 1.4H6.4a9 9 0 0 1 0-1.4zm4.3 0h2.8a5.6 5.6 0 0 1 0 1.4h-2.9c.1-.4.1-.9.1-1.4zM6.4 9.8h3.2C9.4 11.4 8.8 12.8 8 13.6c-.8-.8-1.4-2.2-1.6-3.8z"/></svg>
        <span>www.website.com</span>
      </li>
    </ul>

    <address class="address">
      4820 Larkspur Ave<br>
      Maple Hollow<br>
      Minnesota(MN)
    </address>
  </section>

  <section class="card card--back" aria-label="Card back, black background">
    <div class="brand-square" aria-hidden="true"></div>
    <div class="brand-name">Dario Whitcombe, CPA, LLC</div>
    <div class="brand-tagline">Certified Public Accountant</div>
    <div class="brand-services">Accounting, Tax &amp; Consulting Services</div>
  </section>
</main>
</body>
</html>
```